Accountancy firm needs clean and simple website and optional logo

We need a logo and basic wordpress website design for a Sydney based accountancy firm.
We need a clean and simple logo and website, based on the accounting/finance/tax industry. Simple, credible and official colors.
The logo is expected to be so simple that we have combined into the one job.
If you submit a logo design and we choose it along with someone else's website design you will be paid a bonus of $60. The website design will still win the competition as per normal.
Current website is old and terrible but gives you an idea of the sitemap (super simple) and what they do: www.brookfiscal.com.au
We want original different to normal template looking designs.
We like videos, and like http://www.merivane.com.au/
Feel free to go to clipvault9 and use some videos from there.
We are based in Sydney Australia and in the field of taxation and accounting
We want a clean, formal, credible site, limited pages.
The project is guaranteed, so go for it.
Logo Text
Brook & Associates

```html
<!DOCTYPE html>
<html lang="en">
<head>
<meta charset="utf-8">
<title>Brook &amp; Associates — Tax Accountants</title>
<link rel="stylesheet" href="https://fonts.googleapis.com/css2?family=Raleway:wght@400;500;600&family=Open+Sans:wght@400;600;700&display=swap">
<style>
:root{
  --blue:#0a86d6;
  --blue-dark:#0560b5;
  --blue-nav-top:#12a0ec;
  --ink:#1e1e1e;
  --muted:#6e6e6e;
  --line:#d6d6d6;
  --slate:#a3adb7;
  --footer:#232323;
  --white:#ffffff;
}
*{box-sizing:border-box;margin:0;padding:0}
html,body{width:942px;height:1200px;overflow:hidden;background:var(--white)}
body{position:relative;font-family:"Open Sans",sans-serif;color:var(--ink)}
.abs{position:absolute}

/* header */
.brand-mark{left:149px;top:11px;width:66px;height:66px;background:var(--blue)}
.brand-name{left:226px;top:52px;font-family:"Open Sans",sans-serif;font-weight:700;font-size:11.5px;letter-spacing:.6px;color:var(--ink)}
.brand-tag{left:226px;top:66px;font-size:11px;color:var(--ink)}
.call{right:154px;top:47px;text-align:right}
.call-label{font-size:10px;color:var(--blue);letter-spacing:.2px}
.call-number{display:flex;align-items:center;gap:3px;font-size:18px;color:var(--ink);margin-top:1px}

/* navigation */
.nav{left:147px;top:93px;width:646px;height:34px;display:flex;
  background:linear-gradient(180deg,var(--blue-nav-top),var(--blue) 60%,#0b7fd1)}
.nav a{display:flex;align-items:center;justify-content:center;color:var(--white);
  text-decoration:none;font-size:12.5px;font-weight:600;height:100%}
.nav a.active{background:linear-gradient(180deg,#1281d6,var(--blue-dark))}

/* hero */
.hero{left:145px;top:133px;width:645px;height:344px;
  background:linear-gradient(100deg,#c9d6e3 0%,#b4c5d6 38%,#8c7868 58%,#6e7a7a 78%,#c9a06a 100%)}
.hero-title{left:175px;top:250px;font-family:"Raleway",sans-serif;font-weight:500;font-size:33px;color:#111}
.hero-sub{left:175px;top:296px;font-family:"Raleway",sans-serif;font-weight:600;font-size:17.5px;color:var(--blue);letter-spacing:.3px}
.dots{left:443px;top:457px;display:flex;gap:3px}
.dots span{width:12px;height:12px;border-radius:50%;background:var(--white)}
.dots span.current{background:#9aa9b8}

/* welcome */
.welcome{left:0;width:942px;top:514px;text-align:center;font-family:"Raleway",sans-serif;color:#222}
.welcome h1{font-weight:500;font-size:21.5px;letter-spacing:.3px;line-height:26px}
.welcome h2{font-weight:500;font-size:18.5px;line-height:22px}
.intro{left:171px;top:573px;width:604px;text-align:center;font-size:7.6px;line-height:13.6px;color:var(--muted)}

/* service cards */
.card{top:650px;width:202px;height:231px;border:1px solid var(--line);background:var(--white);text-align:center}
.card-photo{width:100%;height:111px;background:linear-gradient(135deg,#8a8d92,#55595f)}
.card-photo.meeting{background:linear-gradient(135deg,#b9b7b2,#4d525a)}
.card-photo.desk{background:linear-gradient(135deg,#73777d,#4a4f56)}
.card-icon{position:absolute;left:72px;top:25px;width:60px;height:60px}
.card h3{margin-top:15px;font-family:"Raleway",sans-serif;font-weight:500;font-size:15px;color:var(--blue);letter-spacing:.2px}
.card p{margin:6px auto 0;width:172px;font-size:7.6px;line-height:13.8px;color:var(--muted)}
.btn{display:inline-block;margin-top:9px;width:68px;height:19px;line-height:19px;border-radius:2px;
  background:linear-gradient(180deg,#1b8fe0,var(--blue-dark));color:var(--white);font-size:7.8px;font-weight:600}

/* feature panels */
.feature{top:915px;height:145px;display:flex}
.feature-photo{width:149px;height:100%;background:linear-gradient(135deg,#d9dee3,#7c8a98)}
.feature-photo.person{background:linear-gradient(135deg,#9fb1bf,#e5ddd3 55%,#8ea8c4)}
.feature-body{flex:1;padding:23px 16px 0 17px;color:var(--white)}
.feature-body.slate{background:var(--slate)}
.feature-body.blue{background:var(--blue)}
.feature-body h3{font-family:"Raleway",sans-serif;font-weight:400;font-size:16px;letter-spacing:.3px}
.feature-body h4{margin-top:3px;font-size:8.8px;font-weight:600}
.feature-body p{margin-top:9px;font-size:7.6px;line-height:13.7px}

/* footer */
.footer{left:0;top:1110px;width:942px;height:90px;background:var(--footer)}
.footer-links{left:148px;top:1133px;font-size:9.8px;color:var(--white);letter-spacing:.2px}
.footer-copy{left:148px;top:1154px;font-size:8.3px;color:#c8c8c8}
.social{left:684px;top:1132px;display:flex;gap:2px}
.social span{width:24px;height:24px;border-radius:50%;border:1.5px solid #e6e6e6}
</style>
</head>
<body>

<header>
  <div class="abs brand-mark" aria-hidden="true"></div>
  <div class="abs brand-name">BROOK &amp; ASSOCIATES</div>
  <div class="abs brand-tag">tax accountants</div>
  <div class="abs call">
    <div class="call-label">CALL US TODAY</div>
    <div class="call-number">
      <svg width="16" height="16" viewBox="0 0 24 24" aria-hidden="true"><path fill="#0a86d6" d="M6.6 10.8c1.4 2.8 3.8 5.1 6.6 6.6l2.2-2.2c.3-.3.7-.4 1-.2 1.1.4 2.3.6 3.6.6.6 0 1 .4 1 1V20c0 .6-.4 1-1 1C10.6 21 3 13.4 3 4c0-.6.4-1 1-1h3.5c.6 0 1 .4 1 1 0 1.3.2 2.5.6 3.6.1.3 0 .7-.2 1l-2.3 2.2z"/></svg>
      02 9000 4172
    </div>
  </div>
</header>

<nav class="abs nav">
  <a class="active" href="#" style="width:99px">HOME</a>
  <a href="#" style="width:113px">ABOUT US</a>
  <a href="#" style="width:114px">PROJECTS</a>
  <a href="#" style="width:111px">SERVICES</a>
  <a href="#" style="width:89px">NEWS</a>
  <a href="#" style="width:120px">CONTACT</a>
</nav>

<section>
  <div class="abs hero" role="img" aria-label="Photo of a smiling retired couple sitting in wooden deck chairs by a lake"></div>
  <div class="abs hero-title">TAX &amp; ACCOUNTING</div>
  <div class="abs hero-sub">PRAESENT AMET EST DICTUM</div>
  <div class="abs dots"><span class="current"></span><span></span><span></span><span></span></div>
</section>

<section>
  <div class="abs welcome">
    <h1>WELCOME TO BROOK &amp; ASSOCIATES</h1>
    <h2>TAX ACCOUNTANTS</h2>
  </div>
  <p class="abs intro">Mauris vel lacus vitae felis vestibulum volutpat E eu imperdiet ac nisl Cum sociis natoque penatibus et magnis dis parturient montes nascetur ridiculus mus In iaculis facilisis massa Etiam eu urna Sed porta Suspendisse quam leo molestie sed luctus quis feugiat in pede Fusce tellus Sed metus augue convallis et vehicula ut pulvinar eu ante Integer orci tellus tristique vitae consequat nec Vivamus porttitor purus nisi eleifend libero a tempus libero lectus feugiat</p>
</section>

<section>
  <article class="abs card" style="left:157px">
    <div class="card-photo" role="img" aria-label="Photo of a tax form with a pen and glasses"></div>
    <svg class="card-icon" viewBox="0 0 60 60" aria-hidden="true"><circle cx="30" cy="30" r="28.5" fill="none" stroke="#fff" stroke-width="2"/><path d="M22 17h12l5 5v20H22z" fill="none" stroke="#fff" stroke-width="1.8"/><path d="M26 31l8-8" stroke="#fff" stroke-width="1.6"/><circle cx="27" cy="24" r="1.8" fill="none" stroke="#fff" stroke-width="1.3"/><circle cx="33" cy="30" r="1.8" fill="none" stroke="#fff" stroke-width="1.3"/><path d="M25 37l3 3 6-6" fill="none" stroke="#fff" stroke-width="1.8"/></svg>
    <h3>TAX SERVICES</h3>
    <p>rdum nec interdum vel blandit sed nulla In ullamcorper est eget tempor cursus neque mi facilisis volutpat in imperdiet sit</p>
    <span class="btn">READ MORE</span>
  </article>
  <article class="abs card" style="left:372px">
    <div class="card-photo meeting" role="img" aria-label="Photo of an adviser meeting with clients"></div>
    <svg class="card-icon" viewBox="0 0 60 60" aria-hidden="true"><circle cx="30" cy="30" r="28.5" fill="none" stroke="#fff" stroke-width="2"/><rect x="21" y="16" width="18" height="27" rx="2" fill="none" stroke="#fff" stroke-width="1.8"/><rect x="24" y="19" width="12" height="5" fill="#fff"/><g fill="#fff"><rect x="24" y="27" width="3" height="3"/><rect x="28.5" y="27" width="3" height="3"/><rect x="33" y="27" width="3" height="3"/><rect x="24" y="32" width="3" height="3"/><rect x="28.5" y="32" width="3" height="3"/><rect x="33" y="32" width="3" height="3"/><rect x="24" y="37" width="3" height="3"/><rect x="28.5" y="37" width="3" height="3"/><rect x="33" y="37" width="3" height="3"/></g></svg>
    <h3>ACCOUNTING</h3>
    <p>rdum nec interdum vel blandit sed nulla In ullamcorper est eget tempor cursus neque mi facilisis volutpat in imperdie</p>
    <span class="btn">READ MORE</span>
  </article>
  <article class="abs card" style="left:588px">
    <div class="card-photo desk" role="img" aria-label="Photo of hands reviewing financial papers on a desk"></div>
    <svg class="card-icon" viewBox="0 0 60 60" aria-hidden="true"><circle cx="30" cy="30" r="28.5" fill="none" stroke="#fff" stroke-width="2"/><rect x="17" y="19" width="26" height="17" rx="1.5" fill="none" stroke="#fff" stroke-width="1.8"/><path d="M30 36v5M24 42h12" stroke="#fff" stroke-width="1.8"/><g fill="#fff"><rect x="21" y="29" width="2" height="4"/><rect x="24" y="27" width="2" height="6"/><rect x="27" y="25" width="2" height="8"/></g><circle cx="36" cy="27" r="4" fill="#fff"/><path d="M36 27V23a4 4 0 0 1 4 4z" fill="#5a5f66"/></svg>
    <h3>FINANCE SERVICE</h3>
    <p>rdum nec interdum vel blandit sed nulla In ullamcorper est eget tempor cursus neque mi facilisis volutpat in imperdiet sit</p>
    <span class="btn">READ MORE</span>
  </article>
</section>

<section>
  <article class="abs feature" style="left:156px;width:313px">
    <div class="feature-photo" role="img" aria-label="Photo of a business team working around a glass table"></div>
    <div class="feature-body slate">
      <h3>HOW WE WORK</h3>
      <h4>VIEW OUR PROJECTS</h4>
      <p>Rdum nec interdum vel blandit sed nulla In ullamcorper est eget tempor cursus neque mi facilisis volutpat in imperdiet sit</p>
    </div>
  </article>
  <article class="abs feature" style="left:481px;width:312px">
    <div class="feature-photo person" role="img" aria-label="Photo of a team member in a shirt and tie in the office"></div>
    <div class="feature-body blue">
      <h3>OUR TEAM</h3>
      <h4>MEET OUR TEAM MEMBER</h4>
      <p>Rdum nec interdum vel blandit sed nulla In ullamcorper est eget tempor cursus neque mi facilisis volutpat in imperdiet sit</p>
    </div>
  </article>
</section>

<footer>
  <div class="abs footer"></div>
  <div class="abs footer-links">HOME &nbsp;|&nbsp; ABOUT &nbsp;US &nbsp;|&nbsp; SERVICES &nbsp;|&nbsp; OUR PROJECTS &nbsp;|&nbsp; CONTACT US</div>
  <div class="abs footer-copy">© 2015 Company Name &nbsp;All right reserved &nbsp;Term of Use</div>
  <div class="abs social" aria-label="Social links">
    <span style="background:#3aa3dc"></span>
    <span style="background:#2f63b0"></span>
    <span style="background:#1a7fb5"></span>
    <span style="background:#d9412f"></span>
  </div>
</footer>

</body>
</html>
```